Redesign a embroidery design sales site

I wrote http://www.stitchesbymolo.com in php from scratch over many years. I need a web designer to give us an up today more interactive site.

The entire site is template driven, with a top.php and bottom.php on every page.

I need these pages redesigned. I'll take your css and web html and
adapt them to my code:

http://www.stitchesbymolo.com/products/1

http://www.stitchesbymolo.com/points.php

http://www.stitchesbymolo.com/details/appliquesunbonnetscrosses
(appliquesunbennetcrosses is the name of the set, this will change)

http://www.stitchesbymolo.com/buydesigns/appliquesunbonnetscrosses

http://www.stitchesbymolo.com/votedesigns/appliquesunbonnetscrosses

http://www.stitchesbymolo.com/votingresults

Forgot to mention this, www.stitchesbymolo.com/indexsummary.php it is a home page I made a while ago

Reason: I didn't time this well as with Thanksgiving fell in there. I'll be sending out general comments about all designs soon.

Time's running out... can you please submit a design for:

http://www.stitchesbymolo.com/indexsummary.php

http://www.stitchesbymolo.com/products/page1

http://www.stitchesbymolo.com/details/santafriendsrw

http://www.stitchesbymolo.com/buydesigns/santafriendsrw

and

All designs submitted from here will be put infront of 1000's of people to vote for their fav

Love and kisses ...
MoLO

All designers ... submissions seem to stop ... please submit a new update based on what I said.   The final design will be voted by members of my website

3 designers have not been eliminated... 1 day left to get your design to me for my website users to vote on.   Please carefully read what I want.  No big banners.  Nothing is that requires daily/weekly maintence

Target Market(s)

Major are 50+ female grammas with sewing/embroidery machines

Industry/Entity Type

Embroidery

Requirements
Must have
• I want the interaction of http://quillpatchwork.com. That is a cool site. I would like to see a working mock up rather that this cookie cutter stuff.
Should not have
• Should not have a flash/DHTML big banner on the page. Follow the flow of the site now so I can plug and play into my existing code.

```html
<!DOCTYPE html>
<html lang="en">
<head>
<meta charset="utf-8">
<title>StitchesByMoLO.com – Embroidery Designs Online</title>
<link href="https://fonts.googleapis.com/css2?family=Arimo:wght@400;700&display=swap" rel="stylesheet">
<style>
:root{
  --sky:#3fb1e8;
  --sky-light:#8fd3f4;
  --nav-top:#5cc4f2;
  --nav-bottom:#2a9fdc;
  --nav-active:#1f87c4;
  --brand:#2a8fd6;
  --ink:#333333;
  --muted:#777777;
  --line:#dddddd;
  --green:#8cc63f;
  --online:#5a9e1a;
  --alert:#d92b2b;
  --gold:#f2b300;
  --slate:#8ea8bd;
  --footer:#3b3b3b;
  --footer-text:#d6d6d6;
  --price:#1e9be0;
}
*{box-sizing:border-box;margin:0;padding:0}
html,body{width:1025px;height:1200px;overflow:hidden}
body{font-family:"Arimo",Arial,sans-serif;color:var(--ink);font-size:12px;position:relative;
  background:linear-gradient(180deg,var(--sky) 0,var(--sky-light) 120px,#eaf6fc 230px,#ffffff 330px)}
a{color:inherit;text-decoration:none}
.abs{position:absolute}

/* top utility bar */
.utility{position:absolute;left:0;top:0;width:1025px;height:38px;background:#37a9e2;color:#fff;font-size:11px}
.utility .lang-label{position:absolute;right:433px;top:12px;font-size:10.5px;white-space:nowrap}
.lang-select{position:absolute;left:598px;top:7px;width:88px;height:22px;background:#fff;border-radius:3px;color:var(--ink);font-size:11px;display:flex;align-items:center;padding-left:8px;gap:6px}
.lang-select .flag{width:17px;height:11px;background:#3b5a9a;border-radius:1px}
.account-links{position:absolute;left:706px;top:11px;display:flex;gap:10px;align-items:center}
.account-links a{display:flex;align-items:center;gap:5px}
.account-links .sep{opacity:.8}

/* header */
.logo-tab{position:absolute;left:76px;top:55px;width:289px;height:56px;background:#fff;border-radius:6px 6px 0 0}
.logo-name{position:absolute;left:17px;top:9px;font-size:27px;font-weight:700;color:var(--brand);letter-spacing:-.5px}
.logo-tag{position:absolute;left:37px;top:42px;font-size:12px;color:#555}
.stats{position:absolute;right:339px;top:60px;text-align:right;color:#fff;font-weight:700;font-size:13.5px;line-height:20px}
.search{position:absolute;left:707px;top:66px;display:flex;gap:6px}
.search input{width:180px;height:26px;border:1px solid #cfcfcf;border-radius:2px;font:11px "Arimo",sans-serif;color:#999;padding-left:14px}
.search button{width:53px;height:26px;border:1px solid #bbb;background:linear-gradient(#f4f4f4,#d9d9d9);font:11px "Arimo",sans-serif;color:#555}

/* main sheet */
.sheet{position:absolute;left:76px;top:107px;width:873px;height:978px;background:#fff;border-radius:0 6px 0 0}

.main-nav{position:absolute;left:85px;top:121px;width:858px;height:41px;display:flex;border-radius:4px;overflow:hidden;
  background:linear-gradient(var(--nav-top),var(--nav-bottom));box-shadow:0 2px 3px rgba(0,0,0,.15)}
.main-nav a{display:flex;align-items:center;justify-content:center;color:#fff;font-size:12.5px;border-right:1px solid rgba(255,255,255,.35)}
.main-nav a:last-child{border-right:0;justify-content:flex-start;padding-left:16px}
.main-nav a.active{background:linear-gradient(#3cb0ea,var(--nav-active))}

/* login */
.login-box{position:absolute;left:85px;top:177px;width:271px;height:235px;border:1px solid var(--line);border-radius:3px;background:#fff}
.presence{position:absolute;left:50px;top:18px;font-size:11.5px;line-height:18px;white-space:nowrap}
.presence .online{color:var(--online)}
.presence .forums{color:#555}
.presence .alert{color:var(--alert)}
.login-box .divider{position:absolute;left:10px;right:10px;top:66px;border-top:1px solid #e4e4e4}
.login-title{position:absolute;left:28px;top:80px;font-size:16px;color:var(--brand);display:flex;align-items:center;gap:8px}
.field{position:absolute;left:29px;width:233px;height:27px;border:1px solid #ccc;border-radius:2px;font-size:10px;color:#999;padding:8px 0 0 15px;box-shadow:inset 0 1px 2px rgba(0,0,0,.06)}
.register{position:absolute;left:43px;top:194px;color:var(--online);text-decoration:underline;font-size:11.5px}
.btn-login{position:absolute;left:183px;top:186px;width:59px;height:25px;border-radius:2px;background:linear-gradient(#9ab5c7,#6f8ea3);color:#fff;font-size:10.5px;display:flex;align-items:center;justify-content:center}

/* banner */
.banner{position:absolute;left:365px;top:177px;width:577px;height:235px;border:4px solid #e2e2e2;border-radius:2px;background:#f6f6f6;overflow:hidden}
.banner .shirt{position:absolute;right:0;top:0;width:260px;height:227px;background:linear-gradient(110deg,#9a9a9a,#5e5e5e 40%,#3f3f3f)}
.banner .motif{position:absolute;left:14px;top:95px;width:82px;height:82px;transform:rotate(-14deg);background:linear-gradient(#e9e9e9,#bdbdbd);border:2px solid #333}
.banner h2{position:absolute;left:24px;top:52px;font-weight:400;font-size:21px;color:#222}
.banner .sale{position:absolute;left:115px;top:80px;color:#c83232;font-size:26px}
.banner .sale b{font-size:38px}
.banner .view-more{position:absolute;left:220px;top:140px;width:98px;height:30px;border-radius:3px;background:linear-gradient(#555,#2d2d2d);color:#fff;font-size:11.5px;display:flex;align-items:center;justify-content:center;gap:6px}
.banner .arrows{position:absolute;left:15px;top:199px;display:flex;gap:6px}
.banner .arrows span{width:20px;height:20px;border-radius:50%;background:#3a3a3a;display:flex;align-items:center;justify-content:center}

/* newsletter */
.newsletter{position:absolute;left:85px;top:430px;width:271px;height:109px;background:var(--green);border-radius:2px;box-shadow:0 3px 3px rgba(0,0,0,.12)}
.newsletter .dash{position:absolute;inset:5px;border:1px dashed rgba(255,255,255,.7)}
.newsletter .envelope{position:absolute;left:-4px;top:-8px}
.newsletter h3{position:absolute;left:40px;top:12px;font-weight:400;color:#fff;font-size:16px}
.newsletter .mail{position:absolute;left:30px;top:36px;width:233px;height:25px;background:#fff;border:1px solid #d5d5d5;font-size:10.5px;color:#999;padding:7px 0 0 15px}
.newsletter .submit{position:absolute;left:183px;top:68px;width:54px;height:24px;border-radius:2px;background:linear-gradient(#ffd34a,var(--gold));color:#5a3b00;font-size:10.5px;font-weight:700;display:flex;align-items:center;justify-content:center}

/* happy hour */
.happy{position:absolute;left:85px;top:555px;width:271px;height:108px;background:var(--slate);border:3px solid #c6d4df;border-radius:2px}
.happy .off{position:absolute;left:11px;top:22px;width:58px;height:58px;border-radius:50%;background:radial-gradient(circle at 40% 35%,#f04848,#b91717);border:3px solid #fff;color:#fff;font-weight:700;font-size:12.5px;line-height:15px;display:flex;align-items:center;justify-content:center;text-align:center;box-shadow:0 2px 3px rgba(0,0,0,.25)}
.happy p{position:absolute;left:79px;top:17px;width:180px;color:#fff;font-size:13px;line-height:18px;text-align:justify}

.toolbar{position:absolute;left:84px;top:672px;width:272px;height:35px;border-radius:3px;background:linear-gradient(#6fcaf3,#2d9fd9);color:#fff;font-size:14.5px;display:flex;align-items:center;padding-left:28px;gap:9px;box-shadow:0 2px 3px rgba(0,0,0,.15)}

.share{position:absolute;left:89px;top:724px;display:flex;gap:10px}
.share .item{display:flex;gap:4px}
.share .btn{height:17px;border:1px solid #c9c9c9;border-radius:2px;background:linear-gradient(#fff,#ececec);font-size:10.5px;font-weight:700;padding:0 6px;line-height:15px;color:#3b5a9a}
.share .count{height:17px;border:1px solid #ccc;font-size:10px;padding:0 5px;line-height:15px;color:#444;background:#fff}
.rule{position:absolute;left:85px;width:271px;border-top:1px solid #e4e4e4}

.badges{position:absolute;left:92px;top:776px;display:grid;grid-template-columns:88px 88px;gap:8px 5px}
.badges span{height:57px;border-radius:2px}
.badge-red{background:linear-gradient(#b32222,#4a0c0c)}
.badge-gold{background:linear-gradient(#d8b64a,#6e5a19)}
.badge-green{background:linear-gradient(#5c8d2c,#1f3b0f)}
.badge-blue{background:linear-gradient(#3d6fb7,#14284a)}
.rated{position:absolute;left:95px;top:937px;width:116px;height:34px;border-radius:2px;background:linear-gradient(#7a7a7a,#3a3a3a)}
.payments{position:absolute;left:97px;top:1018px;display:flex;align-items:center;gap:6px;font-size:11.5px;color:#555}
.payments .pay-card{width:26px;height:17px;border:1px solid #c8c8c8;border-radius:2px}

/* products */
.products-tab{position:absolute;left:365px;top:430px;width:140px;height:37px;background:#f1f1f1;border-radius:4px 4px 0 0;color:var(--price);font-size:16.5px;padding:10px 0 0 19px}
.products-area{position:absolute;left:365px;top:466px;width:577px;height:618px;background:linear-gradient(#f1f1f1,#fff 120px)}
.product{position:absolute;width:180px;height:170px;background:#fff;border-radius:4px;box-shadow:0 0 3px rgba(0,0,0,.06)}
.product .thumb{position:absolute;left:32px;top:19px;width:118px;height:70px}
.product .price{position:absolute;left:117px;top:6px;width:50px;height:30px;border-radius:15px;background:var(--price);color:#fff;font-weight:700;font-size:13px;display:flex;align-items:center;justify-content:center;box-shadow:0 0 0 2px #fff}
.product .name{position:absolute;left:0;right:0;top:99px;text-align:center;font-size:12px;font-weight:700;color:#333}
.product .actions{position:absolute;left:14px;top:125px;width:153px;height:27px;display:flex;border:1px solid #cfcfcf;border-radius:2px;background:linear-gradient(#fff,#efefef);font-size:10.5px;color:#555;box-shadow:0 1px 2px rgba(0,0,0,.08)}
.product .actions span{display:flex;align-items:center;justify-content:center;gap:5px}
.product .actions span:first-child{width:74px;border-right:1px solid #d5d5d5}
.product .actions span:last-child{flex:1}

.pager{position:absolute;left:619px;top:1055px;display:flex;align-items:center;gap:4px;font-size:10px;color:#444}
.pager .lbl{margin-right:5px}
.pager span.pg{width:20px;height:20px;border-radius:3px;background:#d4d4d4;color:#fff;display:flex;align-items:center;justify-content:center;font-size:9px}
.pager span.pg.current{background:#8c8c8c}

/* footer */
.site-footer{position:absolute;left:0;top:1106px;width:1025px;height:94px;background:var(--footer);color:var(--footer-text);font-size:11.5px}
.footer-links{position:absolute;left:77px;top:29px;display:flex;gap:9px}
.copyright{position:absolute;left:77px;top:59px}
.follow{position:absolute;left:870px;top:36px;display:flex;gap:7px}
.follow span{width:23px;height:23px;border-radius:50%;background:#fff}
</style>
</head>
<body>

<header class="utility">
  <span class="lang-label">Select Language :</span>
  <div class="lang-select"><span class="flag"></span>English
    <svg width="9" height="6" viewBox="0 0 9 6"><path d="M1 1l3.5 3.5L8 1" stroke="#333" stroke-width="1.6" fill="none"/></svg></div>
  <nav class="account-links">
    <a href="#"><svg width="12" height="12" viewBox="0 0 12 12" fill="#fff"><circle cx="6" cy="3.5" r="3"/><path d="M0 12c0-4 3-5 6-5s6 1 6 5z"/></svg>My Account</a><span class="sep">|</span>
    <a href="#"><svg width="13" height="12" viewBox="0 0 13 12" fill="none" stroke="#fff" stroke-width="1.4"><path d="M0 1h2l2 7h7l1.5-5H3"/><circle cx="5" cy="10.5" r="1" fill="#fff"/><circle cx="10" cy="10.5" r="1" fill="#fff"/></svg>My Cart</a><span class="sep">|</span>
    <a href="#"><svg width="10" height="12" viewBox="0 0 10 12"><rect x="0" y="0" width="10" height="12" rx="1" fill="#fff"/><path d="M2 4h6M2 6.5h6M2 9h4" stroke="#37a9e2"/></svg>My Wishlist</a>
  </nav>
</header>

<div class="sheet"></div>

<div class="logo-tab">
  <span class="logo-name">StitchesByMoLO.com</span>
  <span class="logo-tag">Embroidery Designs Online Since 2002</span>
</div>

<div class="stats">23,512 unique designs online<br>1,656 design sets/packs</div>
<form class="search"><input value="Product Search" aria-label="Product Search"><button type="button">SEARCH</button></form>

<nav class="main-nav">
  <a class="active" href="#" style="width:71px">HOME</a>
  <a href="#" style="width:81px">SEARCH</a>
  <a href="#" style="width:64px">FREE</a>
  <a href="#" style="width:89px">TOP LISTS</a>
  <a href="#" style="width:88px">DESIGNS</a>
  <a href="#" style="width:72px">POINTS</a>
  <a href="#" style="width:90px">SUPPLIES</a>
  <a href="#" style="width:89px">ARTICLES</a>
  <a href="#" style="width:92px">SOCIALIZE</a>
  <a href="#" style="width:122px">SUPPORT</a>
</nav>

<aside class="login-box">
  <svg class="abs" style="left:12px;top:19px" width="32" height="32" viewBox="0 0 32 32"><circle cx="11" cy="8" r="5" fill="#5b6a78"/><path d="M2 24c0-7 4-9 9-9s9 2 9 9z" fill="#5b6a78"/><circle cx="20" cy="12" r="6" fill="#222"/><path d="M9 31c0-8 5-11 11-11s11 3 11 11z" fill="#222"/></svg>
  <p class="presence"><span class="online">90 people online,</span> <span class="forums">75 people in the forums</span><br><span class="alert">You are not logged in</span></p>
  <div class="divider"></div>
  <div class="login-title"><svg width="14" height="16" viewBox="0 0 14 16" fill="#2a8fd6"><circle cx="7" cy="4.5" r="4"/><path d="M0 16c0-5 3-7 7-7s7 2 7 7z"/></svg>Customer Log in</div>
  <div class="field" style="top:113px">Username</div>
  <div class="field" style="top:150px">*********</div>
  <a class="register" href="#">REGISTER NOW</a>
  <a class="btn-login" href="#">LOG IN</a>
</aside>

<section class="banner">
  <div class="shirt" role="img" aria-label="Dark grey button shirt with an embroidered horse on the pocket"></div>
  <div class="motif" role="img" aria-label="Horse embroidery design swatch"></div>
  <h2>LAST MINUTE TURKEY DAY</h2>
  <div class="sale">SALE <b>$1.00!</b></div>
  <a class="view-more" href="#">VIEW MORE <svg width="5" height="8" viewBox="0 0 5 8"><path d="M0 0l5 4-5 4z" fill="#fff"/></svg></a>
  <div class="arrows">
    <span><svg width="8" height="10" viewBox="0 0 8 10"><path d="M6 1L2 5l4 4" stroke="#fff" stroke-width="2" fill="none"/></svg></span>
    <span><svg width="8" height="10" viewBox="0 0 8 10"><path d="M2 1l4 4-4 4" stroke="#fff" stroke-width="2" fill="none"/></svg></span>
  </div>
</section>

<section class="newsletter">
  <div class="dash"></div>
  <svg class="envelope" width="38" height="30" viewBox="0 0 38 30"><rect x="2" y="4" width="34" height="22" rx="2" fill="#4aa8e8" transform="rotate(-14 19 15)"/><path d="M4 7l15 10 15-14" stroke="#fff" stroke-width="1.5" fill="none" transform="rotate(-14 19 15)"/></svg>
  <h3>NewsLetter Subscribe</h3>
  <div class="mail">Enter your mail ID</div>
  <a class="submit" href="#">SUBMIT</a>
</section>

<section class="happy">
  <div class="off">50%<br>OFF!</div>
  <p>Any hour can be happy hour, check back every hour to see if it's happy hour, 50% off a set during happy hour!</p>
</section>

<a class="toolbar" href="#">DOWNLOAD OUR TOOLBAR
  <svg width="17" height="17" viewBox="0 0 17 17"><circle cx="8.5" cy="8.5" r="8" fill="#fff"/><path d="M5 8.5h6M8.5 5.5l3 3-3 3" stroke="#2d9fd9" stroke-width="1.8" fill="none"/></svg></a>

<div class="share">
  <div class="item"><span class="btn">Like</span><span class="count">3k</span></div>
  <div class="item"><span class="btn">Post</span><span class="count">316</span></div>
  <div class="item"><span class="btn" style="color:#c8232c">Save</span><span class="count">5</span></div>
</div>
<div class="rule" style="top:760px"></div>

<div class="badges">
  <span class="badge-red"></span><span class="badge-gold"></span>
  <span class="badge-green"></span><span class="badge-blue"></span>
</div>
<div class="rule" style="top:920px"></div>
<div class="rated"></div>

<div class="payments">Payments :
  <span class="pay-card" style="background:#eef3fb"></span>
  <span class="pay-card" style="background:#dfe6f3"></span>
  <span class="pay-card" style="background:#f7d7c6"></span>
  <span class="pay-card" style="background:#f1f1f1"></span>
  <span class="pay-card" style="background:#dfe4f4"></span>
</div>

<div class="products-area"></div>
<div class="products-tab">Our Products</div>

<!-- row 1 -->
<article class="product" style="left:376px;top:482px"><div class="thumb" role="img" aria-label="Yellow cartoon car applique" style="background:linear-gradient(135deg,#f4f4f4,#f4e08a 55%,#e9e9e9)"></div><span class="price">$0.76</span><h3 class="name">Chubby Cars Applique</h3><div class="actions"><span><svg width="11" height="10" viewBox="0 0 13 12" fill="none" stroke="#555" stroke-width="1.4"><path d="M0 1h2l2 7h7l1.5-5H3"/></svg>Buy now</span><span>View more <svg width="4" height="7" viewBox="0 0 4 7"><path d="M0 0l4 3.5L0 7z" fill="#777"/></svg></span></div></article>
<article class="product" style="left:565px;top:482px"><div class="thumb" role="img" aria-label="Sunbonnet girl and cross applique" style="background:linear-gradient(90deg,#d9d9d9,#b83030 40%,#e6d88f 70%,#d9d9d9)"></div><span class="price">$0.76</span><h3 class="name">Applique Sunbonnet</h3><div class="actions"><span><svg width="11" height="10" viewBox="0 0 13 12" fill="none" stroke="#555" stroke-width="1.4"><path d="M0 1h2l2 7h7l1.5-5H3"/></svg>Buy now</span><span>View more <svg width="4" height="7" viewBox="0 0 4 7"><path d="M0 0l4 3.5L0 7z" fill="#777"/></svg></span></div></article>
<article class="product" style="left:754px;top:482px"><div class="thumb" role="img" aria-label="Plant the future recycling design" style="background:linear-gradient(135deg,#f0f0f0,#cfe1b5 45%,#e7cfae 75%,#f0f0f0)"></div><span class="price">$0.76</span><h3 class="name">Recycling</h3><div class="actions"><span><svg width="11" height="10" viewBox="0 0 13 12" fill="none" stroke="#555" stroke-width="1.4"><path d="M0 1h2l2 7h7l1.5-5H3"/></svg>Buy now</span><span>View more <svg width="4" height="7" viewBox="0 0 4 7"><path d="M0 0l4 3.5L0 7z" fill="#777"/></svg></span></div></article>
<!-- row 2 -->
<article class="product" style="left:376px;top:670px"><div class="thumb" role="img" aria-label="Motorcycle line drawing design" style="background:linear-gradient(135deg,#f2f2f2,#c7ccd3 55%,#eeeeee)"></div><span class="price">$0.76</span><h3 class="name">Chubby Cars Applique</h3><div class="actions"><span><svg width="11" height="10" viewBox="0 0 13 12" fill="none" stroke="#555" stroke-width="1.4"><path d="M0 1h2l2 7h7l1.5-5H3"/></svg>Buy now</span><span>View more <svg width="4" height="7" viewBox="0 0 4 7"><path d="M0 0l4 3.5L0 7z" fill="#777"/></svg></span></div></article>
<article class="product" style="left:565px;top:670px"><div class="thumb" role="img" aria-label="Red heart applique with green worm" style="background:linear-gradient(135deg,#f2e6e6,#c81e1e 50%,#efe2e2)"></div><span class="price">$0.76</span><h3 class="name">Applique Sunbonnet</h3><div class="actions"><span><svg width="11" height="10" viewBox="0 0 13 12" fill="none" stroke="#555" stroke-width="1.4"><path d="M0 1h2l2 7h7l1.5-5H3"/></svg>Buy now</span><span>View more <svg width="4" height="7" viewBox="0 0 4 7"><path d="M0 0l4 3.5L0 7z" fill="#777"/></svg></span></div></article>
<article class="product" style="left:754px;top:670px"><div class="thumb" role="img" aria-label="Sleeping bear on a cloud design" style="background:linear-gradient(135deg,#eef1f5,#8a5a3a 50%,#e8edf3)"></div><span class="price">$0.76</span><h3 class="name">Recycling</h3><div class="actions"><span><svg width="11" height="10" viewBox="0 0 13 12" fill="none" stroke="#555" stroke-width="1.4"><path d="M0 1h2l2 7h7l1.5-5H3"/></svg>Buy now</span><span>View more <svg width="4" height="7" viewBox="0 0 4 7"><path d="M0 0l4 3.5L0 7z" fill="#777"/></svg></span></div></article>
<!-- row 3 -->
<article class="product" style="left:376px;top:867px"><div class="thumb" role="img" aria-label="Floral monogram letter design" style="background:linear-gradient(135deg,#f2f2f0,#9fb78a 50%,#ece6d2)"></div><span class="price">$0.76</span><h3 class="name">Chubby Cars Applique</h3><div class="actions"><span><svg width="11" height="10" viewBox="0 0 13 12" fill="none" stroke="#555" stroke-width="1.4"><path d="M0 1h2l2 7h7l1.5-5H3"/></svg>Buy now</span><span>View more <svg width="4" height="7" viewBox="0 0 4 7"><path d="M0 0l4 3.5L0 7z" fill="#777"/></svg></span></div></article>
<article class="product" style="left:565px;top:867px"><div class="thumb" role="img" aria-label="Stitched horse head designs on fabric" style="background:linear-gradient(90deg,#dcdcdc,#bdbdbd 45%,#e9b5bf 70%,#dedede)"></div><span class="price">$0.76</span><h3 class="name">Applique Sunbonnet</h3><div class="actions"><span><svg width="11" height="10" viewBox="0 0 13 12" fill="none" stroke="#555" stroke-width="1.4"><path d="M0 1h2l2 7h7l1.5-5H3"/></svg>Buy now</span><span>View more <svg width="4" height="7" viewBox="0 0 4 7"><path d="M0 0l4 3.5L0 7z" fill="#777"/></svg></span></div></article>
<article class="product" style="left:754px;top:867px"><div class="thumb" role="img" aria-label="Coffee pot with leaves design" style="background:linear-gradient(135deg,#f3f3f3,#a8a8a8 45%,#b94545 65%,#f1f1f1)"></div><span class="price">$0.76</span><h3 class="name">Recycling</h3><div class="actions"><span><svg width="11" height="10" viewBox="0 0 13 12" fill="none" stroke="#555" stroke-width="1.4"><path d="M0 1h2l2 7h7l1.5-5H3"/></svg>Buy now</span><span>View more <svg width="4" height="7" viewBox="0 0 4 7"><path d="M0 0l4 3.5L0 7z" fill="#777"/></svg></span></div></article>

<nav class="pager">
  <span class="lbl">Page 1 of 32</span>
  <span class="pg current">1</span><span class="pg">2</span><span class="pg">3</span><span class="pg">4</span><span class="pg">5</span><span class="pg">6</span><span class="pg">7</span><span class="pg">8</span><span class="pg">»</span>
  <span style="margin:0 3px">...</span><span class="pg">»»</span>
</nav>

<footer class="site-footer">
  <nav class="footer-links">
    <a href="#">Home</a><span>|</span><a href="#">Search</a><span>|</span><a href="#">Free</a><span>|</span><a href="#">Top Lists</a><span>|</span><a href="#">Designs</a><span>|</span><a href="#">Points</a><span>|</span><a href="#">Supplies</a><span>|</span><a href="#">Articles</a><span>|</span><a href="#">Socialize</a><span>|</span><a href="#">Support</a>
  </nav>
  <p class="copyright">Copyright ©&nbsp; 2012 &nbsp;&nbsp;www.stitchesbymolo.com &nbsp;&nbsp;&nbsp;All rights reserved.</p>
  <div class="follow"><span></span><span></span><span></span></div>
</footer>

</body>
</html>
```